Homemaking training schools needs a Business Card design

Designer, Hello!

No special requirements, good-looking enough.
--------------------------------------------------------------------------

Name: Marcus Dole
Chairman
Tel: 0574-71948263
Mobile: 13857420916
Email: kelvora@mailnest.example
Web: www.prt2019.example
Add: No.258, LanpingJie, BeiyuanQu, Ningbo, Zhejiang

LOGO
Ningbo PRT Homemaking Training School

Target Market(s)

pregnant women, mothers, infants, the elderly and families, including cleaning, cooking, nursing training.

Industry/Entity Type

Business

Contact Information for Business Card

Name: Marcus Dole
Chairman
Tel: 0574-71948263
Mobile: 13857420916
Email: kelvora@mailnest.example
Web: www.prt2019.example

LOGO

Font styles to use
Serif
Sans Serif
Decorative

Requirements
Nice to have
• Feels: clean, specifications, safety, comfort, warmth and happiness.

```html
<!DOCTYPE html>
<html lang="en">
<head>
<meta charset="utf-8">
<title>PeiRuiTang Business Card</title>
<link href="https://fonts.googleapis.com/css2?family=Abel&display=swap" rel="stylesheet">
<style>
  :root {
    --page-bg: #e9e6e2;
    --card-light: #f6f5f3;
    --card-light-2: #ecebe8;
    --navy: #1f3b7a;
    --blue-deep: #112f72;
    --blue-mid: #1d4596;
    --pink: #d21a5c;
    --panel-text: #e4eaf7;
  }
  * { margin: 0; padding: 0; box-sizing: border-box; }
  html, body {
    width: 1200px; height: 969px; overflow: hidden;
    background: var(--page-bg);
    font-family: "Abel", sans-serif;
  }
  .business-card {
    position: absolute; left: 100px; top: 201px;
    width: 1000px; height: 566px;
    background: linear-gradient(135deg, var(--card-light), var(--card-light-2));
    overflow: hidden;
    box-shadow: 0 10px 30px rgba(0,0,0,0.12);
  }
  .card-shapes { position: absolute; inset: 0; }
  .brand {
    position: absolute; left: 48px; top: 160px; width: 433px;
    text-align: center;
  }
  .brand-name {
    font-size: 58px; color: var(--navy); letter-spacing: 0.5px; line-height: 1;
  }
  .holder {
    position: absolute; right: 50px; top: 62px; text-align: right;
    color: var(--panel-text);
  }
  .holder-name { font-size: 36px; letter-spacing: 0.5px; line-height: 1.1; }
  .holder-role { font-size: 26px; line-height: 1.3; }
  .contact-list {
    position: absolute; right: 46px; top: 276px; list-style: none;
    color: var(--panel-text); font-size: 27px;
  }
  .contact-item {
    display: flex; align-items: center; justify-content: flex-end;
    height: 39px; gap: 16px;
  }
  .contact-icon { width: 22px; height: 22px; flex: none; }
  .address {
    position: absolute; right: 52px; top: 450px; text-align: right;
    color: var(--panel-text); font-size: 28px; line-height: 37px; letter-spacing: 0.5px;
  }
</style>
</head>
<body>
  <div class="business-card">
    <svg class="card-shapes" viewBox="0 0 1000 566" preserveAspectRatio="none" aria-hidden="true">
      <defs>
        <linearGradient id="panelBlue" x1="0" y1="0" x2="1" y2="1">
          <stop offset="0" stop-color="#1d4596"/>
          <stop offset="1" stop-color="#112f72"/>
        </linearGradient>
      </defs>
      <path d="M748 0 C600 90 440 270 466 566 L1000 566 L1000 0 Z" fill="var(--pink)"/>
      <path d="M778 0 C640 95 520 300 541 566 L1000 566 L1000 0 Z" fill="#f3f1ee"/>
      <path d="M786 0 C650 98 530 302 549 566 L1000 566 L1000 0 Z" fill="url(#panelBlue)"/>
    </svg>

    <div class="brand">
      <span class="brand-name">PeiRuiTang</span>
    </div>

    <div class="holder">
      <p class="holder-name">Marcus Dole</p>
      <p class="holder-role">Chairman</p>
    </div>

    <ul class="contact-list">
      <li class="contact-item">0574-71948263
        <svg class="contact-icon" viewBox="0 0 24 24"><path d="M6.6 3.5l3 3.2-1.8 2.2c1.2 2.6 3.1 4.5 5.6 5.7l2.2-1.8 3.2 3-1.9 3.2C11 18.6 5.4 13 3.4 5.4z" fill="none" stroke="currentColor" stroke-width="1.8" stroke-linejoin="round"/></svg>
      </li>
      <li class="contact-item">13857420916
        <svg class="contact-icon" viewBox="0 0 24 24"><rect x="6.5" y="2.5" width="11" height="19" rx="1.5" fill="none" stroke="currentColor" stroke-width="1.8"/><line x1="10" y1="18" x2="14" y2="18" stroke="currentColor" stroke-width="1.8"/></svg>
      </li>
      <li class="contact-item">kelvora@mailnest.example
        <svg class="contact-icon" viewBox="0 0 24 24"><rect x="3" y="6" width="18" height="12" fill="currentColor"/><path d="M3 6l9 7 9-7" fill="none" stroke="#1a3f8c" stroke-width="1.6"/></svg>
      </li>
      <li class="contact-item">www.prt2019.example
        <svg class="contact-icon" viewBox="0 0 24 24"><circle cx="12" cy="12" r="9" fill="currentColor"/><path d="M8 7c2 1 1 3 3 3s1 3-1 4M15 13c1 1 2 3 0 5" fill="none" stroke="#1a3f8c" stroke-width="1.6"/></svg>
      </li>
    </ul>

    <p class="address">No.258, LanpingJie<br>BeiyuanQu, Ningbo, Zhejiang</p>
  </div>
</body>
</html>
```